Website Design for Solar Panel Company

We are working with a company called VoltaNix.

Some sites to use for content/competitors and inspiration:
https://www.brivaloo.com
https://prod.aws-prod.kelmatrix.com
https://tovarqueworks.net
https://www.quorvex.com/solarpanels

Thank you for taking the time to consider designing a website for us. We are web developers based in Stockton, CA, USA. Most of our projects go through the same process. Understanding this process may help you win a project with us. We custom-code all of our websites in-house. We don’t have any requirements as to what tools you use for your design, but we prefer Figma files. For any design that we label as four-stars, we send it to the client for review. The client picks the final design they want us to use. Once we complete this process, we will continue to show additional clients all the four-star sites and purchase them later. Your designs will have multiple chances to sell. For better chances of success, we ask that you follow these guidelines.

IMAGES:
If you use any images or icons in the design, we ask that you have a link to the asset so we can purchase the image/icon. Most of the designs we submit do not have the customer’s images on them unless they have some great images. Be creative; show us the feeling you are trying to portray with your image choices. Use any royalty-free site you choose. We subscribe to Pendrel and mainly use their images, but we can purchase images outside of Pendrel. PLEASE NOTE: we will not submit designs to clients with watermarks on the images.

FONTS:
We ask that you identify the fonts used in the design. This can be done in a message if you want. We typically use Google Fonts and Pendrel Fonts.

CONTENT:
We're always open to different content and ideas. We often submit designs with stock images so the client can see our vision. We typically take pictures after the website launch to use their images with our vision. Lorem Ipsum is fine for paragraphs, but we ask that you write the headers in correct English. We want to be able to show the vision and identify the sections of the website.

INSPIRATION:
We typically add a couple of links in the brief of websites we like to help you get started in your design.

REVISIONS:
We do not often ask for revisions of the designs unless we see something in the design that may not appeal to the client. If there are slight changes that we want to make, we do that in the development process.

FEEDBACK:
We rarely give feedback on designs during the design process. We are working on many website projects and do not have the time to provide feedback. We usually respond if your request is well thought out and asks specific questions, but a note asking “feedback, please” usually goes unanswered.

```html
<!DOCTYPE html>
<html lang="en">
<head>
<meta charset="utf-8">
<title>VoltaNix – Solar Energy</title>
<link href="https://fonts.googleapis.com/css2?family=Righteous&family=Poppins:ital,wght@0,400;0,500;0,600;0,700;1,400&display=swap" rel="stylesheet">
<style>
:root{
  --green:#6fb52c;
  --green-dark:#4e9a16;
  --green-light:#8cc63f;
  --green-pale:#e3f2d6;
  --ink:#111;
  --body:#555;
  --grey-card:#8e8e8e;
  --white:#fff;
  --black:#000;
}
*{box-sizing:border-box;margin:0;padding:0}
html,body{width:1200px;height:3513px;overflow:hidden;background:var(--white)}
body{font-family:"Poppins",sans-serif;color:var(--ink)}
.page{position:relative;width:1200px;height:3513px;overflow:hidden}
.abs{position:absolute}
.display{font-family:"Righteous",sans-serif;font-weight:400}

/* header + hero */
.hero{position:absolute;left:0;top:0;width:1200px;height:608px;
  background:linear-gradient(180deg,#e9eef2 0%,#f1eadf 35%,#d9c2a0 52%,#9aa3ad 60%,#7d8796 72%,#c99a5d 84%,#8d6b4a 100%)}
.topbar{position:absolute;left:0;top:0;width:1200px;height:8px;background:var(--green)}
.brand{position:absolute;display:flex;align-items:center;gap:10px;font-family:"Poppins",sans-serif;font-weight:700;color:var(--ink);font-size:38px;letter-spacing:.5px}
.brand-dot{width:14px;height:14px;border-radius:50%;background:var(--green)}
.nav{position:absolute;left:365px;top:52px;display:flex;gap:0;font-size:16px;font-weight:500}
.nav a{position:absolute;color:var(--ink);text-decoration:none;white-space:nowrap}
.call-tab{position:absolute;left:880px;top:0;width:47px;height:93px;background:var(--green);border-radius:0 0 24px 24px;display:flex;align-items:flex-end;justify-content:center;padding-bottom:12px}
.call-tab span{width:38px;height:38px;border-radius:50%;background:var(--white);display:flex;align-items:center;justify-content:center;box-shadow:0 0 0 3px var(--green-light)}
.call-label{position:absolute;left:948px;top:45px;font-size:16px;font-weight:500;color:var(--green)}
.call-number{position:absolute;left:948px;top:65px;font-size:16px;color:var(--ink)}
.hero-title{position:absolute;left:112px;top:198px;font-size:41px;line-height:50px;color:var(--ink);letter-spacing:.5px}
.btn{position:absolute;display:flex;align-items:center;justify-content:center;gap:8px;border-radius:6px;font-size:16px;font-weight:500;white-space:nowrap}
.btn-green{background:linear-gradient(180deg,var(--green-light),var(--green-dark));color:var(--ink)}
.btn-outline{border:1.5px solid var(--white);color:var(--white)}
.btn-white{background:var(--white);color:var(--ink)}

/* about */
.about-blob{position:absolute;left:143px;top:703px;width:504px;height:504px;border-radius:50%;background:var(--green-pale)}
.photo{position:absolute;border-radius:22px}
.badge{position:absolute;left:424px;top:1075px;width:123px;height:110px;border-radius:22px;background:var(--black);color:var(--white);text-align:center;padding-top:10px}
.badge b{display:block;font-size:38px;color:var(--green-light);line-height:44px}
.badge small{display:block;font-size:15px;line-height:21px}
.section-title{color:var(--green);font-size:41px;letter-spacing:1px}
.about-sub{position:absolute;left:697px;top:830px;width:420px;font-size:26px;line-height:34px;font-weight:600}
.copy{position:absolute;font-size:15.5px;line-height:25px;color:var(--body);text-align:justify}

/* services */
.services{position:absolute;left:0;top:1316px;width:1200px;height:723px;
  background:linear-gradient(180deg,#cfe8e0 0%,#e4f1e6 45%,#eef6d8 80%,#e6f1d2 100%)}
.card{position:absolute;top:1478px;width:302px;height:475px;border-radius:26px;overflow:hidden;color:var(--white);text-align:center}
.card-green{background:var(--green)}
.card-grey{background:var(--grey-card)}
.card .shot{height:272px;border-radius:26px 26px 26px 26px}
.card h3{font-family:"Righteous",sans-serif;font-weight:400;font-size:22px;line-height:26px;margin-top:16px}
.card p{font-size:14px;line-height:22px;margin:14px 20px 0}
.card .btn{left:77px;top:409px;width:148px;height:41px;font-size:16px}
.arrow-btn{position:absolute;top:1690px;width:50px;height:50px;border-radius:50%;background:var(--black);display:flex;align-items:center;justify-content:center}

/* mission */
.mission-photo{position:absolute;left:571px;top:2126px;width:517px;height:427px;border-radius:44px;background:linear-gradient(180deg,#b9c2c8 0%,#cdd3d6 45%,#5f7a46 70%,#d8dcdf 100%)}
.mission-card{position:absolute;left:113px;top:2179px;width:584px;height:321px;border-radius:44px;background:linear-gradient(160deg,var(--green-light),var(--green-dark));color:var(--white)}

/* testimonials */
.testimonials{position:absolute;left:0;top:2639px;width:1200px;height:583px;background:linear-gradient(180deg,#d6efd0,#e6f3d6)}
.t-card{position:absolute;top:2802px;width:308px;height:263px;background:var(--white);border-radius:16px;border-bottom:4px solid var(--green);box-shadow:0 6px 14px rgba(0,0,0,.08);padding:24px 24px}
.t-quote{font-family:"Righteous",sans-serif;font-size:34px;line-height:34px;color:var(--green)}
.t-text{font-style:italic;font-size:14.5px;line-height:23px;color:var(--body);margin-top:16px;text-align:justify}
.t-person{display:flex;align-items:center;gap:10px;margin-top:14px}
.avatar{width:68px;height:68px;border-radius:50%;background:linear-gradient(135deg,#7a5a46,#3f6e9c)}
.stars{color:#f2b705;font-size:12px;letter-spacing:1px;line-height:12px}
.t-name{font-weight:600;font-size:18px;line-height:24px}
.dot{position:absolute;top:3116px;width:15px;height:15px;border-radius:50%;background:#a9d88a}
.dot.active{width:20px;height:20px;top:3114px;background:var(--green)}

/* footer */
.footer{position:absolute;left:0;top:3222px;width:1200px;height:291px;background:var(--black);color:var(--white)}
.footer-nav{position:absolute;left:0;top:168px;width:1200px;display:flex;justify-content:center;gap:34px;font-size:19px;font-weight:600}
.footer-rule{position:absolute;left:110px;top:231px;width:978px;height:1px;background:#555}
.copyright{position:absolute;left:0;top:244px;width:1200px;text-align:center;font-size:16px}
</style>
</head>
<body>
<div class="page">

  <!-- Hero -->
  <section class="hero" role="img" aria-label="Sunrise over solar panel field with wind turbines and mountains"></section>
  <div class="topbar"></div>
  <div class="brand" style="left:112px;top:38px"><span class="brand-dot"></span>VoltaNix</div>
  <nav class="nav">
    <a style="left:0">Home</a>
    <a style="left:80px">About</a>
    <a style="left:159px">Products</a>
    <a style="left:261px">FAQs</a>
    <a style="left:332px">Review</a>
    <a style="left:419px">Contact</a>
  </nav>
  <div class="call-tab"><span>
    <svg width="20" height="20" viewBox="0 0 24 24"><path fill="#6fb52c" d="M6.6 10.8a15.1 15.1 0 0 0 6.6 6.6l2.2-2.2c.3-.3.7-.4 1-.2 1.1.4 2.3.6 3.6.6.6 0 1 .4 1 1V20c0 .6-.4 1-1 1A17 17 0 0 1 3 4c0-.6.4-1 1-1h3.5c.6 0 1 .4 1 1 0 1.3.2 2.5.6 3.6.1.3 0 .7-.2 1z"/></svg>
  </span></div>
  <div class="call-label">Call Us</div>
  <div class="call-number">+1 555 0142 7788</div>
  <h1 class="hero-title display">Meeting the World Need<br>for Clean Energy by Putting<br>Solar on Every Roof</h1>
  <div class="btn btn-green" style="left:112px;top:368px;width:170px;height:41px">Get Started</div>

  <!-- About -->
  <div class="about-blob"></div>
  <div class="photo" style="left:211px;top:695px;width:191px;height:202px;background:linear-gradient(180deg,#3d6f9a,#9bb5c9 60%,#e9edf0)" role="img" aria-label="House roof covered with solar panels"></div>
  <div class="photo" style="left:424px;top:787px;width:213px;height:264px;background:linear-gradient(180deg,#d8c6a6,#8d8f86 55%,#4a5a66)" role="img" aria-label="Father and child looking at rooftop solar panels"></div>
  <div class="photo" style="left:110px;top:918px;width:292px;height:311px;background:linear-gradient(180deg,#c7c0b4,#b47c5a 40%,#3c4856 75%,#5a6470)" role="img" aria-label="Two installers fitting solar panels on a tiled roof"></div>
  <div class="badge"><b class="display">20+</b><small>Years Of<br>Experiences</small></div>
  <h2 class="section-title display abs" style="left:697px;top:772px">ABOUT US</h2>
  <div class="about-sub">Lorem ipsum dolor sit amet, consectetur</div>
  <p class="copy" style="left:697px;top:908px;width:391px">Lorem ipsum dolor sit amet, consectetur adipiscing elit, sed do eiusmod tempor incididunt ut labore et dolore magna aliqua. Quis ipsum suspendisse ul gravida. Risus commodo viverra maecenas ac cumsan lacus vel facilisis.</p>
  <p class="copy" style="left:697px;top:1041px;width:391px">Lorem ipsum dolor sit amet, consectetur adipiscing elit, sed do eiusmod tempor incididunt</p>
  <div class="btn btn-green" style="left:697px;top:1102px;width:170px;height:41px">Read More
    <svg width="16" height="14" viewBox="0 0 16 14"><path d="M1 7h13M9 2l5 5-5 5" stroke="#111" stroke-width="2" fill="none"/></svg></div>

  <!-- Services -->
  <section class="services"></section>
  <h2 class="section-title display abs" style="left:0;top:1390px;width:1200px;text-align:center">OUR SERVICES</h2>
  <div class="arrow-btn" style="left:36px"><svg width="18" height="18" viewBox="0 0 18 18"><path d="M12 2 5 9l7 7" stroke="#fff" stroke-width="2.5" fill="none"/></svg></div>
  <div class="arrow-btn" style="left:1116px"><svg width="18" height="18" viewBox="0 0 18 18"><path d="m6 2 7 7-7 7" stroke="#fff" stroke-width="2.5" fill="none"/></svg></div>

  <article class="card card-green" style="left:110px">
    <div class="shot" style="background:linear-gradient(180deg,#dfe3e6,#8e9297 60%,#6a4f44)" role="img" aria-label="Workers lifting a solar panel onto a roof"></div>
    <h3>Lorem ipsum dolor sit<br>amet, consect</h3>
    <p>Lorem ipsum dolor sit amet, con sectetur adipiscing elit, sed do</p>
    <div class="btn btn-outline">Read More <svg width="16" height="14" viewBox="0 0 16 14"><path d="M1 7h13M9 2l5 5-5 5" stroke="#fff" stroke-width="2" fill="none"/></svg></div>
  </article>
  <article class="card card-grey" style="left:449px">
    <div class="shot" style="background:linear-gradient(180deg,#8fa27a,#c2b59a 50%,#2f5a46)" role="img" aria-label="Man pointing at a house with solar roof"></div>
    <h3>Lorem ipsum dolor sit<br>amet, consect</h3>
    <p>Lorem ipsum dolor sit amet, con sectetur adipiscing elit, sed do</p>
    <div class="btn btn-outline">Read More <svg width="16" height="14" viewBox="0 0 16 14"><path d="M1 7h13M9 2l5 5-5 5" stroke="#fff" stroke-width="2" fill="none"/></svg></div>
  </article>
  <article class="card card-green" style="left:788px">
    <div class="shot" style="background:linear-gradient(180deg,#4f8fd6,#9cc3ea 45%,#d9dde2)" role="img" aria-label="Electric car charging beside solar panels"></div>
    <h3>Lorem ipsum dolor sit<br>amet, consect</h3>
    <p>Lorem ipsum dolor sit amet, con sectetur adipiscing elit, sed do</p>
    <div class="btn btn-outline">Read More <svg width="16" height="14" viewBox="0 0 16 14"><path d="M1 7h13M9 2l5 5-5 5" stroke="#fff" stroke-width="2" fill="none"/></svg></div>
  </article>

  <!-- Mission -->
  <div class="mission-photo" role="img" aria-label="Model house with solar panels on a grassy base"></div>
  <section class="mission-card">
    <h2 class="display abs" style="left:40px;top:34px;font-size:41px;letter-spacing:1px">OUR MISSION</h2>
    <p class="copy" style="left:42px;top:100px;width:494px;color:var(--white)">Lorem ipsum dolor sit amet, consectetur adipiscing elit, sed do eiusmod tempor incididunt ut labore et dolore magna aliqua. Quis ipsum suspendisse ul gravida. Risus commodo viverra maecenas ac cumsan lacus vel facilisis.</p>
    <div class="btn btn-white" style="left:42px;top:222px;width:170px;height:41px">Read More <svg width="16" height="14" viewBox="0 0 16 14"><path d="M1 7h13M9 2l5 5-5 5" stroke="#111" stroke-width="2" fill="none"/></svg></div>
  </section>

  <!-- Testimonials -->
  <section class="testimonials"></section>
  <h2 class="section-title display abs" style="left:0;top:2714px;width:1200px;text-align:center">OUR TESTIMONIALS</h2>
  <article class="t-card" style="left:112px">
    <div class="t-quote">“…</div>
    <p class="t-text">“Lorem ipsum dolor sit amet, con sectetur adipiscing elit, sed do ei usmod tempor incididunt ut labore et dolore magna aliqua.”</p>
    <div class="t-person"><div class="avatar" role="img" aria-label="Customer portrait"></div><div><div class="stars">★★★★☆</div><div class="t-name">Alexander</div></div></div>
  </article>
  <article class="t-card" style="left:446px">
    <div class="t-quote">“…</div>
    <p class="t-text">“Lorem ipsum dolor sit amet, con sectetur adipiscing elit, sed do ei usmod tempor incididunt ut labore et dolore magna aliqua.”</p>
    <div class="t-person"><div class="avatar" role="img" aria-label="Customer portrait"></div><div><div class="stars">★★★★☆</div><div class="t-name">Alexander</div></div></div>
  </article>
  <article class="t-card" style="left:780px">
    <div class="t-quote">“…</div>
    <p class="t-text">“Lorem ipsum dolor sit amet, con sectetur adipiscing elit, sed do ei usmod tempor incididunt ut labore et dolore magna aliqua.”</p>
    <div class="t-person"><div class="avatar" role="img" aria-label="Customer portrait"></div><div><div class="stars">★★★★☆</div><div class="t-name">Alexander</div></div></div>
  </article>
  <span class="dot active" style="left:551px"></span>
  <span class="dot" style="left:582px"></span>
  <span class="dot" style="left:608px"></span>
  <span class="dot" style="left:634px"></span>

  <!-- Footer -->
  <footer class="footer">
    <div class="brand" style="left:0;top:88px;width:1200px;justify-content:center;color:var(--white)"><span class="brand-dot"></span>VoltaNix</div>
    <nav class="footer-nav"><span>Home</span><span>About</span><span>Products</span><span>FAQs</span><span>Review</span><span>Contact</span></nav>
    <div class="footer-rule"></div>
    <div class="copyright">© 2024 VoltaNix. All Rights Reserved.</div>
  </footer>
</div>
</body>
</html>
```